Gestaltung Mini Katalog für bayerische Polomarke
Gestaltung "Mini" Katalog für bayerische Polomarke
Zielgruppe
Unsere Marke richtet sich an den klassischen Lifestyle Kunden. 20 - 45 Jahre alt, legt Wert auf das Äussere und Kleidung.... Mag es gerne besonders, modern und chic.
Hallo,
wir planen derzeit einen kleinen Katalog von 8-10 Seiten im Format DIN A5 (kein Muss). Präsentiert wird darin die erste bayerische Polomarke K&M reitmode und die aktuellen Kollektionen an Polo-Teamshirts.
Die Fotos dazu werden in den nächsten 14 Tagen entstehen.
Wir suchen nun jemanden, der uns das ganze in eine moderne Gestaltung bringt. Für Vorschläge bitte statt der Fotos alternative Fotos einsetzen.
Unsere Marke bewegt sich im mittleren Preissegment und präsentiert eine ganz besondere Sportart. All das muss in dem Katalog rüber kommen. Neben den Produkt- und Modefotos werden klassische Polobilder integriert, um das Gefühl diesen Sports mit zu vermitteln.
Die Grundfarben sollten sich an denen von K&M reitmode orientieren: schwarz, blau, weiss.... Wobei wir für andere Farben, wenn diese passen bzw. begründet sind auch interessiert sind.

```html
<!DOCTYPE html>
<html lang="de">
<head>
<meta charset="utf-8">
<title>K&amp;M Shirts für Männer</title>
<link rel="stylesheet" href="https://fonts.googleapis.com/css2?family=EB+Garamond:wght@500;600;700&display=swap">
<style>
  :root {
    --bg: #231f20;
    --accent: #1fc3d6;
    --white: #ffffff;
    --card: #ffffff;
    --shirt: #1a1a1a;
  }
  html, body {
    margin: 0;
    padding: 0;
    width: 1198px;
    height: 1200px;
    overflow: hidden;
    background: var(--bg);
  }
  .page {
    position: relative;
    width: 1198px;
    height: 1200px;
    background: var(--bg);
    font-family: "EB Garamond", "Times New Roman", serif;
    color: var(--white);
  }
  .page-title {
    position: absolute;
    left: 0;
    top: 78px;
    width: 663px;
    height: 70px;
    background: var(--accent);
    margin: 0;
    padding-left: 26px;
    box-sizing: border-box;
    font-size: 48px;
    font-weight: 500;
    line-height: 70px;
    color: var(--white);
  }
  .product {
    position: absolute;
    width: 560px;
    text-align: center;
  }
  .product-photo {
    display: block;
    margin: 0 auto;
    width: 332px;
    height: 312px;
    box-sizing: border-box;
    border: 9px solid var(--accent);
    background: var(--card);
    position: relative;
  }
  .product-photo .shape {
    position: absolute;
    inset: 24px 40px;
    background: radial-gradient(ellipse at 50% 45%, #3a3a3a 0%, var(--shirt) 70%);
    border-radius: 14px;
  }
  .product-name {
    margin: 22px 0 0;
    font-size: 27px;
    font-weight: 600;
    line-height: 32px;
  }
  .product-number {
    margin: 2px 0 0;
    font-size: 22px;
    font-weight: 500;
    color: var(--accent);
    line-height: 30px;
  }
  .product-sizes {
    margin: 0;
    font-size: 22px;
    font-weight: 600;
    line-height: 30px;
  }
  .product-price {
    margin: 2px 0 0;
    font-size: 56px;
    font-weight: 600;
    color: var(--accent);
    line-height: 60px;
  }
  .product--tl { left: 23px;  top: 180px; }
  .product--tr { left: 620px; top: 180px; }
  .product--bl { left: 23px;  top: 691px; }
  .product--br { left: 620px; top: 691px; }
</style>
</head>
<body>
<main class="page">
  <h1 class="page-title">K&amp;M Shirts für Männer</h1>

  <article class="product product--tl">
    <div class="product-photo" role="img" aria-label="Produktfoto: schwarzes T-Shirt mit silbernem Polospieler-Motiv"><div class="shape"></div></div>
    <p class="product-name">Shirt für Männer</p>
    <p class="product-number">Best.-Nr.: 080101</p>
    <p class="product-sizes">Größen: S - M - L - XL - XXL</p>
    <p class="product-price">25,00 €</p>
  </article>

  <article class="product product--tr">
    <div class="product-photo" role="img" aria-label="Produktfoto: schwarzes T-Shirt mit blauem Polospieler-Motiv"><div class="shape"></div></div>
    <p class="product-name">Shirt für Männer</p>
    <p class="product-number">Best.-Nr.: 080101a</p>
    <p class="product-sizes">Größen: S - M - L - XL - XXL</p>
    <p class="product-price">25,00 €</p>
  </article>

  <article class="product product--bl">
    <div class="product-photo" role="img" aria-label="Produktfoto: schwarzes kurzärmliges Team-Poloshirt mit Nummer 3"><div class="shape"></div></div>
    <p class="product-name">Original Team Shirt 2008 Herren</p>
    <p class="product-number">Best.-Nr.: 080801</p>
    <p class="product-sizes">Größen: S - M - L - XL - XXL</p>
    <p class="product-price">49,00 €</p>
  </article>

  <article class="product product--br">
    <div class="product-photo" role="img" aria-label="Produktfoto: schwarzes langärmliges Team-Poloshirt mit Nummer 3"><div class="shape"></div></div>
    <p class="product-name">Original Team Shirt 2008 Herren langärmlig</p>
    <p class="product-number">Best.-Nr.: 080803</p>
    <p class="product-sizes">Größen: S - M - L - XL - XXL</p>
    <p class="product-price">65,00 €</p>
  </article>
</main>
</body>
</html>
```